Business Card Design for Property Development Company Director

I am looking for a professional and unforgettable business card design for our Director of our Property Development Company.
Please see attached .pptx file to find out what information to include. You don't have to follow the exact format shown in the file - I am interested to see your creative flair using the information provided.

```html
<!DOCTYPE html>
<html lang="en">
<head>
<meta charset="UTF-8">
<title>Halvern Property Group – Business Card</title>
<link rel="stylesheet" href="https://fonts.googleapis.com/css2?family=Lato:wght@400;700&display=swap">
<style>
  :root {
    --backdrop: #4b4b4b;
    --card-white: #ffffff;
    --brand-blue: #0b57a4;
    --text-grey: #6b6b6b;
    --text-dark: #222222;
    --rule-blue: #8db4de;
    --rule-faint: rgba(255,255,255,0.25);
  }
  * { margin: 0; padding: 0; box-sizing: border-box; }
  html, body { width: 1200px; height: 900px; overflow: hidden; }
  body {
    position: relative;
    background: var(--backdrop);
    font-family: "Lato", sans-serif;
  }
  .card {
    position: absolute;
    top: 200px;
    width: 310px;
    height: 502px;
    box-shadow: 3px 4px 6px rgba(0,0,0,0.45);
  }
  .card-front {
    left: 253px;
    background: var(--card-white);
    border-radius: 62px 0 62px 0;
  }
  .card-back {
    left: 627px;
    background: var(--brand-blue);
    border-radius: 0 62px 0 62px;
    color: #fff;
    text-align: center;
  }
  .brand {
    position: absolute;
    display: flex;
    align-items: center;
    gap: 12px;
    font-weight: 700;
    line-height: 1;
  }
  .brand-mark { width: 52px; height: 52px; flex: none; }
  .brand-name { display: block; font-size: 31px; letter-spacing: 0.5px; }
  .brand-sub { display: block; font-size: 12.5px; letter-spacing: 2.6px; margin-top: 5px; }
  .card-front .brand { left: 35px; top: 124px; color: var(--brand-blue); }
  .card-front .brand-mark { background: var(--brand-blue); }
  .card-back .brand { left: 27px; top: 170px; color: #fff; text-align: left; }
  .card-back .brand-mark { background: #fff; width: 56px; height: 56px; }
  .card-back .brand-name { font-size: 33px; }
  .card-back .brand-sub { font-size: 13px; letter-spacing: 3px; }

  .person { position: absolute; left: 34px; top: 296px; }
  .person-name { font-size: 19px; font-weight: 700; color: var(--brand-blue); }
  .person-role { font-size: 14px; color: var(--text-grey); margin-top: 0; }

  .contacts { position: absolute; left: 33px; top: 357px; list-style: none; }
  .contacts li {
    display: flex; align-items: center; gap: 5px;
    font-size: 14px; color: var(--text-grey); height: 18px;
  }
  .contacts svg { width: 11px; height: 11px; fill: var(--brand-blue); flex: none; }

  .rule-front {
    position: absolute; left: 32px; top: 424px; width: 236px; height: 1px;
    background: var(--rule-blue);
  }
  .licence { position: absolute; left: 32px; top: 434px; font-size: 14.5px; color: var(--text-dark); }
  .licence-label { color: var(--brand-blue); margin-right: 4px; }

  .tagline {
    position: absolute; left: 0; right: 0; top: 243px;
    font-size: 15px; line-height: 18px; text-transform: uppercase;
  }
  .rule-back {
    position: absolute; left: 42px; top: 405px; width: 224px; height: 1px;
    background: var(--rule-faint);
  }
  .invite { position: absolute; left: 0; right: 0; top: 420px; font-size: 15px; line-height: 18px; }
</style>
</head>
<body>
  <section class="card card-front" aria-label="Business card front">
    <div class="brand">
      <span class="brand-mark"></span>
      <span><span class="brand-name">HALVERN</span><span class="brand-sub">PROPERTY GROUP</span></span>
    </div>
    <div class="person">
      <p class="person-name">DANIEL MARSH</p>
      <p class="person-role">Director</p>
    </div>
    <ul class="contacts">
      <li><svg viewBox="0 0 12 12"><path d="M1 4c0-1.5 2-3 5-3s5 1.5 5 3l-2.5 1-1-1.5h-3L3.5 5 1 4zM2.5 6h7l1 5h-9z"/></svg>0400 318 562</li>
      <li><svg viewBox="0 0 12 12"><path d="M0 2h12v1.2L6 7 0 3.2zM0 4.5l6 3.8 6-3.8V10H0z"/></svg>daniel@halvern.com.au</li>
      <li><svg viewBox="0 0 12 12"><circle cx="6" cy="6" r="5.5"/><path d="M3 4h3l-1 3 2 1-1 3-2-3zM7 2l2 1 1 3-2-1z" fill="#fff"/></svg>www.halvern.com.au</li>
    </ul>
    <div class="rule-front"></div>
    <p class="licence"><span class="licence-label">Real Estate Lic:</span> 5201934 &amp; 5201935</p>
  </section>

  <section class="card card-back" aria-label="Business card back">
    <div class="brand">
      <span class="brand-mark"></span>
      <span><span class="brand-name">HALVERN</span><span class="brand-sub">PROPERTY GROUP</span></span>
    </div>
    <p class="tagline">Property Development<br>&amp; Site Acquisition Specialists</p>
    <div class="rule-back"></div>
    <p class="invite">Ask me about our INVESTMENT &amp;<br>PARTNERSHIP opportunities</p>
  </section>
</body>
</html>
```